Jolly Paws Business Card Update

I have a business card which I love. I want to keep the same logo, colours, font and style. I want to upgrade the scripting and remove some elements and add others.
On the front side under Services - remove the existing wording and insert - Providing individual coaching strategies to create happy, healthy and social canine companions
Under Denise Carvell amend the current wording to read: Qualified in Dog Behavioural Training, Natural Animal Healthcare and Animal Health Science
On the reverse side to remove the web address.

```html
<!DOCTYPE html>
<html lang="en">
<head>
<meta charset="utf-8">
<title>Jolly Paws Business Card</title>
<link rel="stylesheet" href="https://fonts.googleapis.com/css2?family=Open+Sans:ital,wght@0,400;0,600;0,700;1,400&family=Arimo:wght@400&display=swap">
<style>
  :root {
    --backdrop: #2c2c2c;
    --paper: #eceded;
    --paper-edge: #dfe0e2;
    --navy: #233a8c;
    --royal: #1f5fb5;
    --sky: #0a86cc;
    --brand-blue: #1a6db3;
    --red: #c41f24;
    --deep-red: #8e1a1e;
    --cream: #efe7d2;
    --ink: #3a3a3a;
    --white: #ffffff;
  }
  * { box-sizing: border-box; margin: 0; padding: 0; }
  html, body { width: 1138px; height: 1200px; overflow: hidden; }
  body { background: var(--backdrop); position: relative; font-family: "Open Sans", sans-serif; }

  .card {
    position: absolute;
    width: 375px;
    height: 620px;
    border-radius: 14px;
    overflow: hidden;
    text-align: center;
  }
  .card--front { left: 156px; top: 276px; background: linear-gradient(160deg, #f4f4f4, var(--paper) 60%, var(--paper-edge)); }
  .card--back { left: 577px; top: 274px; background: linear-gradient(200deg, var(--navy) 0%, var(--royal) 45%, #1c63b8 100%); }

  .brand-mark {
    position: absolute;
    left: 50%;
    top: 62px;
    width: 148px;
    height: 148px;
    margin-left: -74px;
    border-radius: 50%;
    background: var(--cream);
    border: 9px solid var(--red);
  }
  .brand-name {
    position: absolute;
    left: 0; right: 0;
    top: 222px;
    font-family: "Open Sans", sans-serif;
    font-weight: 600;
    font-size: 36px;
    letter-spacing: 1px;
    line-height: 44px;
  }
  .card--front .brand-name { color: var(--navy); }
  .card--back .brand-name { color: var(--white); top: 226px; }

  .tagline {
    position: absolute;
    left: 0; right: 0;
    top: 266px;
    font-family: "Arimo", sans-serif;
    font-size: 18px;
    line-height: 22px;
  }
  .card--front .tagline { color: var(--deep-red); }
  .card--back .tagline { color: var(--white); top: 270px; }

  .holder-name {
    position: absolute; left: 0; right: 0; top: 340px;
    font-size: 24px; font-weight: 600; color: var(--brand-blue);
  }
  .qualifications {
    position: absolute; left: 0; right: 0; top: 373px;
    font-size: 15px; font-style: italic; line-height: 21px; color: #4a4a4a;
  }
  .contact-divider { position: absolute; left: 75px; top: 469px; width: 225px; height: 24px; }
  .contact-list {
    position: absolute; left: 0; right: 0; top: 507px;
    list-style: none; font-size: 15px; line-height: 23px; color: var(--ink);
  }

  .services-band {
    position: absolute; left: 0; right: 0; top: 370px; height: 130px;
    background: linear-gradient(90deg, #8f1a1e 0%, #d41f25 50%, #8f1a1e 100%);
  }
  .services-label {
    position: absolute; left: 50%; top: 356px; width: 188px; height: 30px; margin-left: -94px;
    background: var(--white); border-radius: 15px;
    box-shadow: 0 3px 0 #1d4f9a;
    font-weight: 700; font-size: 18px; letter-spacing: 2.5px; line-height: 30px; color: #1b2a55;
  }
  .services-text {
    position: absolute; left: 30px; right: 30px; top: 406px;
    font-family: "Arimo", sans-serif; font-size: 15px; line-height: 20px;
    text-transform: uppercase; color: var(--white);
  }
  .mission-band {
    position: absolute; left: 0; right: 0; top: 500px; bottom: 0;
    background: linear-gradient(180deg, #1a74c2, var(--sky));
  }
  .mission-text {
    position: absolute; left: 40px; right: 40px; top: 526px;
    font-family: "Arimo", sans-serif; font-size: 16px; line-height: 19px; color: var(--white);
  }
</style>
</head>
<body>

  <section class="card card--front">
    <div class="brand-mark"></div>
    <h1 class="brand-name">JOLLY PAWS</h1>
    <p class="tagline">HAPPY DOGS, HAPPY OWNERS</p>
    <h2 class="holder-name">Denise Carvell</h2>
    <p class="qualifications">Qualified in Dog Behavioural Training,<br>Natural Animal Healthcare and<br>Animal Health Science</p>

    <svg class="contact-divider" viewBox="0 0 225 24" aria-hidden="true">
      <line x1="0" y1="12" x2="62" y2="12" stroke="#c41f24" stroke-width="2"/>
      <line x1="163" y1="12" x2="225" y2="12" stroke="#c41f24" stroke-width="2"/>
      <g fill="#1f5fb5" stroke="#c41f24" stroke-width="1.6">
        <circle cx="87" cy="12" r="10.5"/>
        <circle cx="112.5" cy="12" r="10.5"/>
        <circle cx="138" cy="12" r="10.5"/>
      </g>
      <path d="M82 10 q5 -5 10 0 l-2 2 h-6 z M83 13 h8 v3 h-8 z" fill="#fff"/>
      <rect x="107" y="8" width="11" height="8" fill="#fff"/>
      <path d="M107 8 l5.5 4.5 l5.5 -4.5" fill="none" stroke="#1f5fb5" stroke-width="1.2"/>
      <g fill="none" stroke="#fff" stroke-width="1.1">
        <circle cx="138" cy="12" r="5.5"/>
        <ellipse cx="138" cy="12" rx="2.4" ry="5.5"/>
        <line x1="132.5" y1="12" x2="143.5" y2="12"/>
      </g>
    </svg>

    <ul class="contact-list">
      <li>0412 706358</li>
      <li>jollypaws1@mailbox.com</li>
      <li>www.jollypaws1.com</li>
    </ul>
  </section>

  <section class="card card--back">
    <div class="brand-mark"></div>
    <h1 class="brand-name">JOLLY PAWS</h1>
    <p class="tagline">HAPPY DOGS, HAPPY OWNERS</p>
    <div class="services-band"></div>
    <div class="services-label">SERVICES</div>
    <p class="services-text">Providing individual coaching strategies to create happy, healthy and social canine companions</p>
    <div class="mission-band"></div>
    <p class="mission-text">Promoting communication and connection between dogs and their families</p>
  </section>

</body>
</html>
```